Executive Taxi firm with Chauffeur service Website

I have my domain name registered and I have started to work on my site but I am struggling. I am just about to get a logo for the company and need a web site that clearly represents the fact we are an executive/luxury brand in private hire vehicles. We offer airport transfers, train station transfers, seaport transfers, holiday transfers and business to business pick up and drop off.

Target Market(s)

Corporate people, holidaymakers looking for a luxury start their holiday. VIPs' and celebrities.

Number of Pages Required

5+ page

Font styles to use
Serif
Sans Serif
Decorative
Script

Colors

Designer to choose colors to be used in the design.

Requirements
Must have
• Home Page, Services, About Us, VIP and Contact us
• Please see www.brivomotors.co.uk I have started it but not happy with it at all.
Nice to have
• Booking form or enquiry form.

```html
<!DOCTYPE html>
<html lang="en">
<head>
<meta charset="utf-8">
<title>Brivo Motors – Executive Private Hire</title>
<link rel="stylesheet" href="https://fonts.googleapis.com/css2?family=Raleway:wght@400;600;700;800&family=Open+Sans:wght@400;600;700&display=swap">
<style>
:root{
  --orange:#f7a11a;
  --ink:#222;
  --text:#444;
  --muted:#777;
  --line:#d6d6d6;
  --dark:#141414;
  --white:#fff;
  --card:#f4f4f4;
}
*{box-sizing:border-box;margin:0;padding:0}
html,body{width:1200px;height:3077px;overflow:hidden}
body{position:relative;background:var(--white);font-family:"Open Sans",Arial,sans-serif;color:var(--text)}
.abs{position:absolute}
.brand{display:flex;align-items:center;gap:14px}
.brand-dot{width:30px;height:30px;border-radius:50%;background:var(--orange)}
.brand-name{font-family:"Raleway",Arial,sans-serif;font-weight:700;font-size:31px;line-height:33px;color:var(--ink);text-transform:uppercase}
/* header */
.site-header{top:0;left:0;width:1200px;height:125px}
.site-header .brand{position:absolute;left:110px;top:28px}
.lang{position:absolute;right:110px;top:30px;display:flex;align-items:center;gap:14px;font-size:15px;font-weight:600;color:var(--ink)}
.lang-select{width:66px;height:26px;border:1px solid #999;font-size:14px;padding:2px 6px;display:flex;justify-content:space-between;align-items:center}
.nav{position:absolute;right:110px;top:74px;display:flex;gap:40px;font-family:"Raleway",Arial,sans-serif;font-size:15px;font-weight:600;color:var(--ink)}
.nav .active{font-weight:800}
/* hero */
.hero{top:125px;left:0;width:1200px;height:535px;background:linear-gradient(100deg,#2a2a2a 0%,#5c5a58 35%,#a89d92 60%,#6a7f95 85%,#3d4450 100%)}
.booking{position:absolute;left:110px;top:56px;width:395px;height:435px;background:var(--white);padding:20px 34px;box-shadow:0 2px 10px rgba(0,0,0,.25)}
.booking h2{font-family:"Raleway",Arial,sans-serif;font-weight:600;font-size:30px;text-align:center;color:var(--ink)}
.booking .sub{font-size:11px;text-align:center;color:var(--muted);margin-top:2px}
.booking label{display:block;font-size:13px;color:var(--ink);margin-top:16px;margin-bottom:5px}
.field{height:28px;border:1px solid #bbb;font-size:10px;color:#888;padding:7px 8px;display:flex;justify-content:space-between;align-items:center}
.row{display:flex;gap:20px}.row>div{flex:1}
.btn-search{margin-top:22px;height:42px;background:var(--orange);color:var(--white);font-family:"Raleway",Arial,sans-serif;font-weight:700;font-size:19px;text-align:center;line-height:42px;letter-spacing:.5px}
.hero-title{position:absolute;left:560px;top:310px;font-family:"Raleway",Arial,sans-serif;font-weight:800;font-size:58px;line-height:60px;color:var(--white);text-transform:uppercase}
.hero-sub{position:absolute;left:563px;top:445px;font-family:"Raleway",Arial,sans-serif;font-weight:600;font-size:24px;color:var(--white)}
.scroll-cue{left:577px;top:632px;width:46px;height:46px;border-radius:50%;background:var(--white);display:flex;align-items:center;justify-content:center}
/* split sections */
.section-title{font-family:"Raleway",Arial,sans-serif;font-weight:700;font-size:32px;color:var(--ink);text-transform:uppercase}
.underline{width:100px;height:3px;background:var(--orange);margin:14px 0 30px}
.copy{font-size:14px;line-height:31px;color:var(--text);text-align:justify}
.btn-outline{display:inline-block;margin-top:32px;border:2px solid var(--orange);border-radius:24px;color:var(--orange);font-family:"Raleway",Arial,sans-serif;font-weight:600;font-size:17px;padding:10px 26px}
.photo{border:1px solid var(--line)}
/* services */
.services-head{top:1636px;left:0;width:1200px;text-align:center}
.services-head h2{font-family:"Raleway",Arial,sans-serif;font-weight:700;font-size:32px;color:var(--ink)}
.services-head p{font-size:14px;color:var(--ink);margin-top:10px}
.service-card{top:1735px;width:316px;height:376px;background:var(--card);text-align:center}
.service-card.raised{background:var(--white);box-shadow:0 10px 30px rgba(0,0,0,.15)}
.service-card .img{height:200px}
.service-card h3{font-family:"Raleway",Arial,sans-serif;font-weight:700;font-size:19px;color:var(--ink);margin-top:30px;text-transform:uppercase}
.service-card .tag{color:var(--orange);font-size:14px;margin-top:8px}
.service-card p{font-size:14px;line-height:26px;color:var(--text);margin:10px 22px 0}
.arrow{top:1825px}
/* contact */
.contact{top:2200px;left:0;width:1200px;height:525px;background:linear-gradient(180deg,#1b1b1b,#0c0c0c)}
.contact h2{position:absolute;top:75px;width:100%;text-align:center;font-family:"Raleway",Arial,sans-serif;font-weight:700;font-size:32px;color:var(--white)}
.contact .lead{position:absolute;top:128px;left:300px;width:600px;text-align:center;font-size:14px;line-height:28px;color:var(--white)}
.input{position:absolute;border:2px solid var(--white);color:var(--white);font-size:12px;padding:0 20px;display:flex;align-items:center}
.btn-submit{position:absolute;left:533px;top:415px;width:133px;height:42px;border-radius:22px;background:var(--orange);border:2px solid var(--white);color:var(--white);font-family:"Raleway",Arial,sans-serif;font-weight:700;font-size:18px;text-align:center;line-height:38px}
/* footer */
.foot-col{top:2790px}
.foot-col h4{font-family:"Raleway",Arial,sans-serif;font-weight:700;font-size:16px;color:var(--ink);margin-bottom:22px}
.foot-col li{list-style:none;font-size:13px;color:var(--ink);margin-bottom:12px;display:flex;align-items:center;gap:10px}
.social{width:36px;height:36px;border-radius:50%;background:var(--orange)}
.news-input{width:235px;height:40px;border:1px solid #999;font-size:13px;padding:0 16px;display:flex;justify-content:space-between;align-items:center;color:var(--ink);margin-top:18px}
.btn-small{display:inline-block;margin-top:14px;border:2px solid var(--orange);border-radius:20px;color:var(--orange);font-family:"Raleway",Arial,sans-serif;font-weight:700;font-size:14px;padding:7px 20px}
.legal{top:3005px;left:110px;width:990px;border-top:1px solid var(--line);padding-top:20px;display:flex;justify-content:space-between;font-size:13px;color:var(--ink)}
</style>
</head>
<body>

<header class="abs site-header">
  <div class="brand"><span class="brand-dot"></span><span class="brand-name">Brivo<br>Motors</span></div>
  <div class="lang">Language :<span class="lang-select">Eng <svg width="10" height="6"><path d="M0 0h10L5 6z" fill="#333"/></svg></span></div>
  <nav class="nav"><span class="active">Home</span><span>Services</span><span>About Us</span><span>VIP</span><span>Contact Us</span></nav>
</header>

<section class="abs hero" role="img" aria-label="Mother and daughter smiling in the back seat of a car">
  <form class="booking">
    <h2>Book your Ride</h2>
    <p class="sub">Airport Transfers, Taxis and Executives Cars in UK</p>
    <label>Pick-up Location</label><div class="field">Enter The Pick-up Location...</div>
    <label>Drop-off Location</label><div class="field">Enter The Drop-off Location...</div>
    <div class="row">
      <div><label>Date</label><div class="field">02/10/2018<svg width="11" height="11"><rect x="1" y="2" width="9" height="8" fill="none" stroke="#888"/><path d="M1 4h9" stroke="#888"/></svg></div></div>
      <div><label>Time</label><div class="field">20:18<svg width="11" height="11"><circle cx="5.5" cy="5.5" r="4.5" fill="none" stroke="#888"/><path d="M5.5 3v3h2" stroke="#888" fill="none"/></svg></div></div>
    </div>
    <div class="row">
      <div><label>Passengers</label><div class="field">1<svg width="12" height="10"><circle cx="6" cy="3" r="2.5" fill="#888"/><path d="M1 10a5 4 0 0 1 10 0z" fill="#888"/></svg></div></div>
      <div><label>Return Journey</label><div class="field">Return Journey<svg width="8" height="5"><path d="M0 0h8L4 5z" fill="#888"/></svg></div></div>
    </div>
    <div class="btn-search">Search</div>
  </form>
  <h1 class="hero-title">Executive<br>Brivo Motors</h1>
  <p class="hero-sub">Private Hire, Chauffeur and taxi service in UK</p>
</section>
<div class="abs scroll-cue"><svg width="14" height="9"><path d="M1 1l6 6 6-6" fill="none" stroke="#333" stroke-width="2"/></svg></div>

<section class="abs" style="top:780px;left:110px;width:470px">
  <h2 class="section-title">Always here for you</h2>
  <div class="underline"></div>
  <p class="copy">We provide airport transfers to and from all major UK airports, seaports, train station transfers and an executive business to business transfer service. Whether you have an individual or group transfer request, our company-owned fleet offers a choice of options to suit your needs, from luxury saloons and SUV's to 9-seat luxury transporters.</p>
  <span class="btn-outline">View Cars</span>
</section>
<div class="abs photo" style="top:788px;left:622px;width:466px;height:299px;background:linear-gradient(135deg,#eeeeee,#d9d9d9)" role="img" aria-label="Smartphone showing a taxi booking app over a street map"></div>

<div class="abs photo" style="top:1210px;left:110px;width:465px;height:298px;background:linear-gradient(180deg,#9aa7a8 0%,#6f7d75 45%,#1e1e1e 70%,#0e0e0e 100%)" role="img" aria-label="Driver's hands on the steering wheel of a luxury car on a mountain road"></div>
<section class="abs" style="top:1200px;left:615px;width:475px">
  <h2 class="section-title">Chauffeur</h2>
  <div class="underline"></div>
  <p class="copy">We provide a chauffeur at door-to-door convenience from your home, office or hotel straight to any destination of your choice. Pre-booked or last minute we aim to cover any transport requirement. Allports and train station service; All pickups from arrivals will of been briefed as to your exact pickup point, or your chauffeur will be waiting with a name board.</p>
  <span class="btn-outline">Read More</span>
</section>

<div class="abs services-head"><h2>OUR SERVICES</h2><p>We provide the perfect solution and exactly your needs</p></div>
<svg class="abs arrow" style="left:44px" width="14" height="22"><path d="M11 2L3 11l8 9" fill="none" stroke="#999" stroke-width="2"/></svg>
<svg class="abs arrow" style="left:1150px" width="14" height="22"><path d="M3 2l8 9-8 9" fill="none" stroke="#999" stroke-width="2"/></svg>
<article class="abs service-card raised" style="left:110px">
  <div class="img" role="img" aria-label="Travellers with luggage beside a car outside an airport" style="background:linear-gradient(135deg,#8a8f96,#c9c4bc 50%,#5a5f66)"></div>
  <h3>Airport Transfers</h3><div class="tag">Lorem Ipsum dolor Ut</div>
  <p>Sed ut perspiciatis unde omnis iste natus tarsoeit volupt accusant dolor volupt..</p>
</article>
<article class="abs service-card" style="left:442px">
  <div class="img" role="img" aria-label="Yellow train at a platform with taxis waiting" style="background:linear-gradient(135deg,#c9c7a0,#8c8f94 50%,#3f4348)"></div>
  <h3>Train Station Transfers</h3><div class="tag">Lorem Ipsum dolor Ut</div>
  <p>Sed ut perspiciatis unde omnis iste natus tarsoeit volupt accusant dolor volupt..</p>
</article>
<article class="abs service-card" style="left:774px">
  <div class="img" role="img" aria-label="Dark saloon car parked by a harbour" style="background:linear-gradient(180deg,#5a6580 0%,#9a8a86 45%,#3d5f6e 75%,#2a2f36 100%)"></div>
  <h3>Seaport Transfers</h3><div class="tag">Lorem Ipsum dolor Ut</div>
  <p>Sed ut perspiciatis unde omnis iste natus tarsoeit volupt accusant dolor volupt..</p>
</article>

<section class="abs contact" role="img" aria-label="Dark night street with taxis in the background">
  <h2>GET IN TOUCH WITH US</h2>
  <p class="lead">Please email any requests and we will endeavour to reply within the hour. Alternatively if you have an urgent request please call on the number provided.</p>
  <div class="input" style="left:305px;top:208px;width:282px;height:54px">First Name</div>
  <div class="input" style="left:613px;top:208px;width:282px;height:54px">Last Name</div>
  <div class="input" style="left:305px;top:268px;width:282px;height:54px">Email Address</div>
  <div class="input" style="left:613px;top:268px;width:282px;height:54px">Phone Number</div>
  <div class="input" style="left:305px;top:328px;width:590px;height:66px">Journey Details</div>
  <div class="btn-submit">Submit</div>
</section>

<div class="abs foot-col" style="left:112px">
  <h4>Contact Us On</h4>
  <ul>
    <li><svg width="14" height="14"><path d="M3 1l3 3-2 2a8 8 0 0 0 4 4l2-2 3 3-2 2C6 13 1 8 1 3z" fill="#f7a11a"/></svg>07700 900418</li>
    <li><svg width="14" height="11"><rect width="14" height="11" rx="1" fill="#f7a11a"/><path d="M0 1l7 5 7-5" fill="none" stroke="#fff"/></svg>info@brivomotors.co.uk</li>
  </ul>
  <div style="display:flex;gap:14px;margin-top:4px"><span class="social"></span><span class="social"></span></div>
</div>
<div class="abs foot-col" style="left:342px">
  <h4>Quick Links</h4>
  <ul>
    <li>» Home</li><li>» Services</li><li>» About Us</li><li>» VIP</li><li>» Contact Us</li>
  </ul>
</div>
<div class="abs foot-col" style="left:587px;width:250px">
  <h4 style="margin-bottom:8px">Join Our Newsletter</h4>
  <p style="font-size:13px;line-height:24px;color:var(--ink)">Join our newsletter and find<br>ut more.</p>
  <div class="news-input">Enter The Email<svg width="14" height="11"><rect x=".5" y=".5" width="13" height="10" fill="none" stroke="#333"/><path d="M.5 .5l6.5 5 6.5-5" fill="none" stroke="#333"/></svg></div>
  <span class="btn-small">Send Now</span>
</div>
<div class="abs brand" style="left:880px;top:2820px"><span class="brand-dot"></span><span class="brand-name">Brivo<br>Motors</span></div>

<footer class="abs legal"><span>Copyright 2018 &nbsp;All Rights Reserved.</span><span>Terms of Use &nbsp; | &nbsp;Privacy Policy</span></footer>

</body>
</html>
```